Site for entrepreneurs/small businesses needs Logo, Homepage

Looking for a logo, either an icon, or stylized text, or a combination of both, and a home page design which fits with it. The logo will be for use on the public website as well as for printed collateral (business cards, post cards, brochures and various other marketing materials).

The site is called Orbitwell (Orbitwell.example). This is to be a national, and eventually an international brand. The new service will provide an easy-to-use platform for entrepreneurs to build their business and web presence together in an integrated way which allows them to focus on their core competency.

The site/service will be dead-simple to use, A/B/C, 1/2/3. We will want some sort of "Get started for FREE" promotional space to collect the person's email address with multiple points of interest which guide the user back to this one call to action: sign up for free. We will feature editorial/blog stories, customer testimonials, and present several key features the the reader just can't live without if they are starting a new business.

Criteria:
* Refer to our comparable sites/logos in the design document attached
* Incorporate our color scheme (but complementary colors welcome)
* No Serif fonts!
* No photo-realistic elements for logo
* Logo must present well in gray scale and/or black/white (for printed materials)
* Strokes/borders that are wider to promote simplicity (vs. thin/precise lines which promote technical complexity)

Inspirations:
* Creative/Custom (but legible) fonts
* Excitement, energetic, jumping for joy
* Karate / Ninja / Power / Precision
* Dance Moves
* Regional influences: California, Silicon Valley, West Coast, Surf City, Beaches, Sunset
* Simple/easy, no-brainer solutions

Target Market(s)

Small Businesses / Entrepreneurs

Logo Text

Orbitwell or Orbitwell.example

Number of Pages Required

1 page

Font styles to use
Sans Serif
Decorative

Requirements
Must have
• See the attached style guide (PDF)

```html
<!DOCTYPE html>
<html lang="en">
<head>
<meta charset="utf-8">
<title>Orbitwell</title>
<link href="https://fonts.googleapis.com/css2?family=Exo+2:wght@400;500;600;700&display=swap" rel="stylesheet">
<style>
:root{
  --purple:#6f0fc0;
  --purple-deep:#4a0a8c;
  --purple-ink:#2b0c55;
  --orange:#f08a1c;
  --btn:#c4560f;
  --lav:#e9dcfb;
  --text:#333;
  --white:#fff;
  --bar:#2a0a4a;
}
*{box-sizing:border-box;margin:0;padding:0}
html,body{width:1200px;height:3214px;overflow:hidden}
body{position:relative;background:var(--white);font-family:"Exo 2",sans-serif;color:var(--text)}
.abs{position:absolute}
.bg{position:absolute;left:0;top:0}
.brand{left:75px;top:30px;display:flex;align-items:center;gap:12px;color:var(--white);font-weight:700;font-size:34px;letter-spacing:.5px}
.brand-dot{width:30px;height:30px;border-radius:50%;background:var(--orange)}
.nav{right:75px;top:36px;display:flex;gap:30px;list-style:none}
.nav a{color:var(--white);text-decoration:none;font-size:14px;font-weight:600;letter-spacing:.6px;text-transform:uppercase}
.hero-title{left:128px;top:162px;color:var(--orange);font-size:42px;font-weight:700}
.hero-sub{left:112px;top:228px;color:var(--white);font-size:27px;font-weight:700}
.email{left:107px;top:291px;width:318px;height:48px;border-radius:24px;background:var(--white);padding-left:26px;line-height:48px;font-size:15px;font-weight:600;color:#555}
.btn{display:inline-block;background:var(--btn);color:var(--white);text-align:center;font-weight:700;text-transform:uppercase;border-radius:30px;text-decoration:none}
.btn-lg{width:188px;height:54px;line-height:54px;font-size:16px}
.signup{left:171px;top:355px}
.art{position:absolute}
.h2{font-size:40px;font-weight:700;color:var(--purple-ink);text-transform:uppercase}
.body{font-size:14.5px;line-height:24px;text-align:justify;color:#333}
.who{left:664px;top:668px;width:398px}
.who .body{margin-top:16px}
.who .btn{margin-top:30px}
.blog{left:135px;top:1190px;width:396px}
.blog .body{margin-top:14px}
.meta{display:flex;gap:24px;margin-top:14px;font-size:14px;color:var(--purple)}
.meta span{display:flex;align-items:center;gap:6px}
.btn-blog{left:129px;top:1468px;width:178px}
.features-title{left:0;width:1200px;top:1652px;text-align:center;color:var(--white);font-size:38px;font-weight:700;text-transform:uppercase}
.grid{left:75px;top:1727px;width:1050px;display:grid;grid-template-columns:repeat(4,248px);column-gap:19px;row-gap:22px}
.card{height:330px;background:var(--white);border-radius:20px;text-align:center;padding-top:22px}
.card-icon{display:block;width:96px;height:96px;margin:0 auto}
.card h3{margin-top:34px;font-size:19px;font-weight:700;color:var(--purple-deep)}
.card p{margin:8px auto 0;width:200px;font-size:15px;line-height:24px;color:#333}
.card .btn{margin-top:14px;width:124px;height:44px;line-height:44px;font-size:12px}
.testi{left:128px;top:2520px;width:356px;color:var(--white)}
.testi h2{font-size:38px;font-weight:700;text-transform:uppercase;letter-spacing:1px}
.testi p{margin-top:10px;font-size:14.5px;line-height:23px;text-align:justify}
.testi .name{margin-top:12px;font-size:24px;font-weight:700}
.dots{left:397px;top:2731px;display:flex;gap:8px}
.dots i{width:15px;height:15px;border-radius:50%;background:var(--purple-ink)}
.foot-col{top:2918px}
.foot-col h4{font-size:22px;font-weight:700;color:var(--purple-ink);text-transform:uppercase;margin-bottom:14px}
.foot-col ul{list-style:none}
.foot-col li{font-size:15px;line-height:33px;color:#222;display:flex;align-items:center;gap:14px}
.links{left:77px}
.links-2{left:291px;top:2957px}
.follow{left:534px}
.contact{left:870px}
.soc{width:14px;height:14px;border-radius:50%;background:var(--purple-ink);flex:none}
.ico{width:18px;height:18px;flex:none}
.bar{left:0;top:3150px;width:1200px;height:64px;background:var(--bar);color:var(--white);text-align:center;line-height:64px;font-size:15px}
</style>
</head>
<body>

<svg class="bg" width="1200" height="3214" viewBox="0 0 1200 3214" aria-hidden="true">
  <defs>
    <linearGradient id="heroGrad" x1="0" y1="0" x2="1" y2="1">
      <stop offset="0" stop-color="#4a0a8c"/><stop offset="1" stop-color="#7a12c9"/>
    </linearGradient>
    <linearGradient id="midGrad" x1="0" y1="0" x2="0" y2="1">
      <stop offset="0" stop-color="#7a12c9"/><stop offset="1" stop-color="#6a0db8"/>
    </linearGradient>
  </defs>
  <path fill="url(#heroGrad)" d="M0 0H1200V275C1110 240 1020 110 850 92C690 78 640 250 560 390C480 520 250 545 0 470Z"/>
  <path fill="url(#midGrad)" d="M0 1490C90 1545 260 1565 400 1530C620 1480 900 1470 1200 1445V2458C1010 2470 720 2440 575 2520C485 2575 525 2700 505 2780C470 2880 250 2870 0 2830Z"/>
</svg>

<header>
  <div class="abs brand"><span>Orbitwell</span><span class="brand-dot"></span></div>
  <ul class="abs nav">
    <li><a href="#">About Us</a></li>
    <li><a href="#">Our Blog Story</a></li>
    <li><a href="#">Customer Testimonials</a></li>
    <li><a href="#">Features</a></li>
    <li><a href="#">Contact Us</a></li>
  </ul>
</header>

<section class="hero">
  <h1 class="abs hero-title">HELLO WORLD</h1>
  <p class="abs hero-sub">GET STARTED FOR FREE</p>
  <div class="abs email">EMAIL ID</div>
  <a class="abs btn btn-lg signup" href="#">Sign up for free</a>
  <svg class="art" style="left:625px;top:125px" width="450" height="405" viewBox="0 0 450 405" role="img" aria-label="Illustration of a team meeting around a dashboard screen">
    <defs><radialGradient id="gHero" cx="50%" cy="50%" r="55%"><stop offset="0" stop-color="#e2d4f8"/><stop offset=".7" stop-color="#f1ebfb"/><stop offset="1" stop-color="#fff" stop-opacity="0"/></radialGradient></defs>
    <ellipse cx="225" cy="205" rx="225" ry="200" fill="url(#gHero)"/>
  </svg>
</section>

<section>
  <svg class="art" style="left:0;top:557px" width="520" height="540" viewBox="0 0 520 540" role="img" aria-label="Illustration of a person working at a computer desk">
    <defs><linearGradient id="gDesk" x1="0" y1="0" x2="1" y2="1"><stop offset="0" stop-color="#c03ae6"/><stop offset="1" stop-color="#4f10ad"/></linearGradient></defs>
    <path fill="url(#gDesk)" d="M0 40C120 -10 300 20 420 110C530 200 540 380 430 470C330 545 170 520 60 430C30 410 10 400 0 395Z"/>
  </svg>
  <div class="abs who">
    <h2 class="h2">Who we are</h2>
    <p class="body">Donec nisl et mi auctor potenti id metus ipsum. Molestie phasellus proin vehicula maecenas sem nunc congue tincidunt. Vestibulum magnis magna rutrum animi vitae. At id nisl. Porta proin integer tortor quia fringilla. Luctus mauris nec. Magna tortor ullamcorper est massa eu. Tristique erat sed. Ultricies arcu quam</p>
    <a class="btn btn-lg" href="#">Read more</a>
  </div>
</section>

<section>
  <div class="abs blog">
    <h2 class="h2">Blog stories</h2>
    <p class="body">Donec nisl et mi auctor potenti id metus ipsum. Molestie phasellus proin vehicula maecenas sem nunc congue tincidunt. Vestibulum magnis magna rutrum animi vitae. At id nisl. Porta proin integer tortor quia fringilla. Luctus mauris nec. Magna tortor ullamcorper est massa eu. Tristique erat sed. Ultricies arcu quam</p>
    <div class="meta">
      <span><svg width="16" height="14" viewBox="0 0 16 14"><path d="M8 13L1.5 6.5A3.6 3.6 0 0 1 8 2.5A3.6 3.6 0 0 1 14.5 6.5Z" fill="none" stroke="#6f0fc0" stroke-width="1.6"/></svg>12 people like</span>
      <span><svg width="14" height="14" viewBox="0 0 14 14"><rect x="1" y="2.5" width="12" height="10.5" rx="1" fill="none" stroke="#6f0fc0" stroke-width="1.6"/><path d="M1 6H13M4 1V4M10 1V4" stroke="#6f0fc0" stroke-width="1.6"/></svg>23-05-2018</span>
      <span><svg width="14" height="14" viewBox="0 0 14 14"><circle cx="7" cy="4.5" r="3" fill="none" stroke="#6f0fc0" stroke-width="1.6"/><path d="M1.5 13.5C2 9.5 12 9.5 12.5 13.5" fill="none" stroke="#6f0fc0" stroke-width="1.6"/></svg>By Mara</span>
    </div>
  </div>
  <a class="abs btn btn-lg btn-blog" href="#">More stories</a>
  <svg class="art" style="left:605px;top:1140px" width="585" height="405" viewBox="0 0 585 405" role="img" aria-label="Isometric illustration of people working on a blog platform">
    <defs><linearGradient id="gBlog" x1="0" y1="0" x2="0" y2="1"><stop offset="0" stop-color="#f1e8fd"/><stop offset="1" stop-color="#cfb2f3"/></linearGradient></defs>
    <ellipse cx="292" cy="215" rx="290" ry="175" fill="url(#gBlog)"/>
    <path d="M2 215A290 175 0 0 0 582 215V240A290 175 0 0 1 2 240Z" fill="#b994ec"/>
  </svg>
</section>

<section>
  <h2 class="abs features-title">Key features</h2>
  <div class="abs grid">
    <div class="card">
      <svg class="card-icon" viewBox="0 0 96 96" role="img" aria-label="Team icon"><circle cx="30" cy="34" r="11" fill="#5cbf5e"/><circle cx="66" cy="34" r="11" fill="#5cbf5e"/><path d="M12 72C12 56 48 56 48 72Z" fill="#3f9a48"/><path d="M48 72C48 56 84 56 84 72Z" fill="#3f9a48"/><circle cx="48" cy="46" r="13" fill="#7fd47a"/><path d="M24 88C24 66 72 66 72 88Z" fill="#4fae52"/></svg>
      <h3>Team Work</h3><p>Lorem magna volutpat. Ullam neque lobortis. Feugiat vitae at. Vel sem laoreet</p><a class="btn" href="#">Read more</a></div>
    <div class="card">
      <svg class="card-icon" viewBox="0 0 96 96" role="img" aria-label="Pie chart icon"><ellipse cx="44" cy="60" rx="36" ry="18" fill="#5a1aa8"/><ellipse cx="44" cy="54" rx="36" ry="18" fill="#8a3ad8"/><path d="M50 46V18A36 18 0 0 1 88 38Z" fill="#f3a03a"/><path d="M50 46L88 38V46Z" fill="#d9601a"/><path d="M44 50V24A36 18 0 0 0 22 30Z" fill="#e8402f"/></svg>
      <h3>Business Statistics</h3><p>Lorem magna volutpat. Ullam neque lobortis. Feugiat vitae at. Vel sem laoreet</p><a class="btn" href="#">Read more</a></div>
    <div class="card">
      <svg class="card-icon" viewBox="0 0 96 96" role="img" aria-label="Megaphone icon"><path d="M14 38H34L70 18V78L34 58H14Z" fill="#dcdcdc"/><rect x="14" y="38" width="20" height="20" fill="#bdbdbd"/><ellipse cx="70" cy="48" rx="10" ry="30" fill="#c0304a"/><path d="M22 58L30 80H40L34 58Z" fill="#9e9e9e"/></svg>
      <h3>Marketing</h3><p>Lorem magna volutpat. Ullam neque lobortis. Feugiat vitae at. Vel sem laoreet</p><a class="btn" href="#">Read more</a></div>
    <div class="card">
      <svg class="card-icon" viewBox="0 0 96 96" role="img" aria-label="Paper plane icon"><path d="M8 46L88 18L50 80L42 56Z" fill="#ececec"/><path d="M42 56L88 18L50 80Z" fill="#c9c9c9"/><path d="M42 56L46 72L50 62Z" fill="#a9a9a9"/></svg>
      <h3>Easy to Use</h3><p>Lorem magna volutpat. Ullam neque lobortis. Feugiat vitae at. Vel sem laoreet</p><a class="btn" href="#">Read more</a></div>
    <div class="card">
      <svg class="card-icon" viewBox="0 0 96 96" role="img" aria-label="Entrepreneur icon"><circle cx="48" cy="14" r="9" fill="#2a2a2a"/><path d="M36 28H60L58 62H38Z" fill="#2a2a2a"/><path d="M44 28H52L50 48H46Z" fill="#c0304a"/><rect x="40" y="62" width="6" height="28" fill="#2a2a2a"/><rect x="50" y="62" width="6" height="28" fill="#2a2a2a"/></svg>
      <h3>Entrepreneurs</h3><p>Lorem magna volutpat. Ullam neque lobortis. Feugiat vitae at. Vel sem laoreet</p><a class="btn" href="#">Read more</a></div>
    <div class="card">
      <svg class="card-icon" viewBox="0 0 96 96" role="img" aria-label="Building blocks icon"><path d="M8 44L24 36L40 44L24 52Z" fill="#d8d8d8"/><path d="M34 34L50 26L66 34L50 42Z" fill="#e8402f"/><path d="M56 44L72 36L88 44L72 52Z" fill="#f3a03a"/><path d="M30 58L46 50L62 58L46 66Z" fill="#8a4ad8"/><path d="M30 58V64L46 72V66Z" fill="#5a1aa8"/><path d="M62 58V64L46 72V66Z" fill="#6a2ab8"/></svg>
      <h3>Build Business</h3><p>Lorem magna volutpat. Ullam neque lobortis. Feugiat vitae at. Vel sem laoreet</p><a class="btn" href="#">Read more</a></div>
    <div class="card">
      <svg class="card-icon" viewBox="0 0 96 96" role="img" aria-label="Headphones icon"><path d="M16 58A32 32 0 0 1 80 58" fill="none" stroke="#333" stroke-width="8"/><rect x="10" y="52" width="20" height="28" rx="8" fill="#444"/><rect x="66" y="52" width="20" height="28" rx="8" fill="#444"/><rect x="16" y="56" width="10" height="20" rx="4" fill="#777"/></svg>
      <h3>Support</h3><p>Lorem magna volutpat. Ullam neque lobortis. Feugiat vitae at. Vel sem laoreet</p><a class="btn" href="#">Read more</a></div>
    <div class="card">
      <svg class="card-icon" viewBox="0 0 96 96" role="img" aria-label="Web signal icon"><path d="M14 78V58A20 20 0 0 1 34 78Z" fill="#2a35b8"/><path d="M14 44A34 34 0 0 1 48 78H38A24 24 0 0 0 14 54Z" fill="#3d4fd8"/><path d="M14 30A48 48 0 0 1 62 78H52A38 38 0 0 0 14 40Z" fill="#4f64e8"/><path d="M14 16A62 62 0 0 1 76 78H66A52 52 0 0 0 14 26Z" fill="#6a7cf0"/></svg>
      <h3>Web Services</h3><p>Lorem magna volutpat. Ullam neque lobortis. Feugiat vitae at. Vel sem laoreet</p><a class="btn" href="#">Read more</a></div>
  </div>
</section>

<section>
  <div class="abs testi">
    <h2>Testimonials</h2>
    <p>"Donec nisl et mi auctor potenti id metus ipsum. Molestie phasellus proin vehicula maecenas sem nunc congue tincidunt. Vestibulum magnis magna rutrum animi vitae"</p>
    <p class="name">- Nora Vale</p>
  </div>
  <div class="abs dots"><i></i><i></i><i></i></div>
  <svg class="art" style="left:630px;top:2495px" width="545" height="380" viewBox="0 0 545 380" role="img" aria-label="Illustration of people around a laptop with customer reviews">
    <defs><radialGradient id="gTesti" cx="50%" cy="55%" r="55%"><stop offset="0" stop-color="#c9a9f2"/><stop offset=".6" stop-color="#e6d8fb"/><stop offset="1" stop-color="#fff" stop-opacity="0"/></radialGradient></defs>
    <ellipse cx="272" cy="200" rx="272" ry="180" fill="url(#gTesti)"/>
  </svg>
</section>

<footer>
  <div class="abs foot-col links">
    <h4>Links</h4>
    <ul><li>Home</li><li>About Us</li><li>Our Blog Stories</li><li>Key Features</li><li>Customer Testimonials</li></ul>
  </div>
  <div class="abs foot-col links-2">
    <ul><li>Login</li><li>Sign Up</li></ul>
  </div>
  <div class="abs foot-col follow">
    <h4>Follow us</h4>
    <ul><li><span class="soc"></span>Circlebook</li><li><span class="soc"></span>Chirper</li><li><span class="soc"></span>Linkpro</li><li><span class="soc"></span>Snapgram</li></ul>
  </div>
  <div class="abs foot-col contact">
    <h4>Contact us</h4>
    <ul>
      <li><svg class="ico" viewBox="0 0 18 18"><path d="M9 17C4 11 3.5 9 3.5 7A5.5 5.5 0 0 1 14.5 7C14.5 9 14 11 9 17Z" fill="#222"/><circle cx="9" cy="7" r="2" fill="#fff"/></svg>#123, Lorium ipsum,</li>
      <li><span class="ico"></span>Dolor Amit,</li>
      <li><span class="ico"></span>City.</li>
      <li><svg class="ico" viewBox="0 0 18 18"><path d="M4 2L7 2L8 6L6 7.5C7 10 8 11 10.5 12L12 10L16 11L16 14C16 15 15 16 14 16C8 15.5 2.5 10 2 4C2 3 3 2 4 2Z" fill="#222"/></svg>0800-555 0190</li>
      <li><svg class="ico" viewBox="0 0 18 18"><rect x="1.5" y="4" width="15" height="11" rx="1" fill="#222"/><path d="M2 5L9 10L16 5" fill="none" stroke="#fff" stroke-width="1.4"/></svg>support@orbitwell.example</li>
    </ul>
  </div>
  <div class="abs bar">Copyright © 2018 . www.orbitwell.example</div>
</footer>

</body>
</html>
```